Brintel Works - Fast, Efficient and Gas Mainteance for Domestic, Commercial and Industrial clients

We are in the process of purchasing a new business and would like to get a new logo and business card.
Business is a gas maintenance business that also does new gas installations.
Has been established since 1988.
Services include:
Install all types of gas appliances & equipment inc. hot water units
Maintain / repair / replace all types of gas appliances & equipment

Target Market(s)

Domestic, Commercial and Industrial clients

Industry/Entity Type

Business

Contact Information for Business Card

admin@brintelworks.com.au
07 3918 4726
Brintel Works PTY LTD

Logo Text

Gas Fitting & Plumbing Maintenance Specialists

Font styles to use
Sans Serif

Requirements
Must have
• Logo
• Business name, contact number, email address, web address
• Domestic | Commercial | Industrial Est Since 1988
Nice to have
• Possibly a black card with a flame logo to one side
Should not have
• Spelling errors

```html
<!DOCTYPE html>
<html lang="en">
<head>
<meta charset="utf-8">
<title>Brintel Works PTY LTD – Business Card</title>
<link rel="stylesheet" href="https://fonts.googleapis.com/css2?family=Archivo:wght@800&family=Questrial&display=swap">
<style>
  :root {
    --backdrop: #6b4a35;
    --card-white: #ffffff;
    --card-black: #050505;
    --ink: #111111;
    --flame-orange: #f26a21;
    --flame-amber: #f7a21b;
    --flame-red: #ec2f2a;
    --on-dark: #ffffff;
  }
  * { box-sizing: border-box; margin: 0; padding: 0; }
  html, body { width: 1200px; height: 1000px; overflow: hidden; }
  body {
    position: relative;
    background: var(--backdrop);
    font-family: "Questrial", "Century Gothic", sans-serif;
    color: var(--ink);
  }
  .card {
    position: absolute;
    left: 265px;
    width: 665px;
    height: 397px;
    border-radius: 22px;
    overflow: hidden;
    box-shadow: 0 6px 14px rgba(0,0,0,0.35);
  }
  .card--front { top: 73px; background: var(--card-white); }
  .card--back  { top: 532px; background: var(--card-black); }

  .brand-mark {
    position: absolute;
    border-radius: 50%;
    background: var(--flame-orange);
  }
  .card--front .brand-mark { left: 42px; top: 56px; width: 86px; height: 86px; }
  .card--back  .brand-mark { left: 58px; top: 62px; width: 256px; height: 256px; }

  .brand-name {
    position: absolute;
    font-family: "Archivo", "Arial Black", sans-serif;
    font-weight: 800;
    line-height: 1;
    text-transform: uppercase;
  }
  .card--front .brand-name { left: 158px; top: 86px; color: var(--ink); }
  .card--back  .brand-name { left: 352px; top: 168px; color: var(--on-dark); }
  .brand-name__main { display: block; letter-spacing: 1px; }
  .brand-name__sub  { display: block; letter-spacing: 2.4px; }
  .card--front .brand-name__main { font-size: 31px; }
  .card--front .brand-name__sub  { font-size: 12.5px; margin-top: 5px; }
  .card--back  .brand-name__main { font-size: 42px; }
  .card--back  .brand-name__sub  { font-size: 17px; margin-top: 8px; letter-spacing: 3.2px; }

  .contact { position: absolute; left: 158px; top: 186px; }
  .contact__name {
    color: var(--flame-orange);
    font-size: 18px;
    margin-bottom: 14px;
  }
  .contact__row {
    display: flex;
    align-items: center;
    gap: 8px;
    font-size: 15.5px;
    line-height: 22px;
  }
  .contact__row svg { width: 14px; height: 14px; fill: var(--flame-orange); }
  .services {
    position: absolute;
    left: 158px;
    top: 276px;
    font-size: 15.5px;
    line-height: 20.5px;
    width: 300px;
  }
  .accent-band {
    position: absolute;
    left: 0; bottom: 0;
    width: 100%;
    height: 18px;
    background: linear-gradient(90deg, var(--flame-red), var(--flame-amber) 48%, var(--flame-red));
  }
</style>
</head>
<body>
  <section class="card card--front" aria-label="Business card front">
    <div class="brand-mark"></div>
    <div class="brand-name">
      <span class="brand-name__main">Brintel</span>
      <span class="brand-name__sub">Works PTY LTD</span>
    </div>
    <div class="contact">
      <p class="contact__name">Mark Denholm</p>
      <p class="contact__row">
        <svg viewBox="0 0 24 24" aria-hidden="true"><path d="M6.6 10.8a15.1 15.1 0 0 0 6.6 6.6l2.2-2.2a1 1 0 0 1 1-.25 11.4 11.4 0 0 0 3.6.57 1 1 0 0 1 1 1V20a1 1 0 0 1-1 1A17 17 0 0 1 3 4a1 1 0 0 1 1-1h3.5a1 1 0 0 1 1 1c0 1.25.2 2.45.57 3.6a1 1 0 0 1-.25 1z"/></svg>
        07 3918 4726
      </p>
      <p class="contact__row">
        <svg viewBox="0 0 24 24" aria-hidden="true"><path d="M2 5h20v14H2z M2 5l10 8 10-8" /></svg>
        admin@brintelworks.com.au
      </p>
    </div>
    <p class="services">
      Install all types of gas appliances &amp; equipment inc. hot water units<br>
      Maintain / repair / replace all types of gas appliances &amp; equipment
    </p>
    <div class="accent-band"></div>
  </section>

  <section class="card card--back" aria-label="Business card back">
    <div class="brand-mark"></div>
    <div class="brand-name">
      <span class="brand-name__main">Brintel</span>
      <span class="brand-name__sub">Works PTY LTD</span>
    </div>
  </section>
</body>
</html>
```